Business Cards - Brightpath Horizon

need to design unique business card for my mortgage business. I need to design credit card style business card for my business or any unique idea that you might have

Target Market(s)

Home Loan customers

Industry/Entity Type

Mortgage Brokerage

Contact Information for Business Card

please design credit card style or very unique style business card

Colors

Designer to choose colors to be used in the design.

Requirements
Must have
• Name
• position
• Phone number
• fax number
• email address
• website address
• social media address
• All above fields will be provided once design in finalised

```html
<!DOCTYPE html>
<html lang="en">
<head>
<meta charset="UTF-8">
<title>Brightpath Horizon – Business Card</title>
<link rel="stylesheet" href="https://fonts.googleapis.com/css2?family=Work+Sans:wght@400;500&display=swap">
<style>
  :root {
    --backdrop: #161616;
    --card: #262626;
    --card-edge: #2c2c2c;
    --stripe: #2aa5e3;
    --brand-blue: #3b5fc8;
    --name-blue: #1f5fc4;
    --accent-orange: #f08c1e;
    --text-light: #f2f2f2;
    --icon-blue: #2a62c9;
  }
  * { box-sizing: border-box; margin: 0; padding: 0; }
  html, body {
    width: 1200px; height: 900px; overflow: hidden;
    background: var(--backdrop);
  }
  .canvas {
    position: relative; width: 1200px; height: 900px;
    display: flex; flex-direction: column; align-items: center;
    justify-content: center; gap: 48px;
  }
  .card {
    position: relative; width: 660px; height: 377px;
    background: linear-gradient(160deg, var(--card-edge), var(--card));
    overflow: hidden;
    box-shadow: 0 10px 30px rgba(0,0,0,.45);
  }
  .card__stripe {
    position: absolute; left: 0; right: 0; bottom: 0; height: 9px;
    background: var(--stripe);
  }
  .brand { display: flex; align-items: center; gap: 12px; }
  .brand__mark { width: 16px; height: 16px; background: var(--accent-orange); flex: none; }
  .brand__name {
    font-family: "Work Sans", sans-serif; font-weight: 500;
    color: var(--brand-blue); letter-spacing: .02em; line-height: 1.1;
  }

  /* front */
  .card--front { display: flex; align-items: center; justify-content: center; padding-bottom: 9px; }
  .card--front .brand__name { font-size: 44px; }

  /* back */
  .card--back { display: flex; align-items: center; padding: 0 0 9px 0; }
  .card--back .brand { width: 270px; margin-left: 34px; justify-content: center; }
  .card--back .brand__mark { width: 12px; height: 12px; }
  .card--back .brand__name { font-size: 25px; }
  .divider {
    width: 2px; height: 214px; background: var(--accent-orange);
    margin: 0 30px 0 24px; flex: none;
  }
  .contact { font-family: "Work Sans", sans-serif; color: var(--text-light); }
  .contact__name {
    font-size: 21px; font-weight: 500; color: var(--name-blue);
    text-transform: uppercase; letter-spacing: .04em;
  }
  .contact__role { font-size: 15px; letter-spacing: .06em; margin-top: 2px; }
  .contact__address { font-size: 14px; line-height: 1.35; margin-top: 14px; letter-spacing: .03em; }
  .contact__list { list-style: none; margin-top: 14px; }
  .contact__item {
    display: flex; align-items: center; gap: 12px;
    font-size: 15px; line-height: 1.6; letter-spacing: .02em; white-space: nowrap;
  }
  .contact__icon { width: 14px; height: 14px; fill: var(--icon-blue); flex: none; }
</style>
</head>
<body>
<main class="canvas">

  <section class="card card--front" aria-label="Card front">
    <div class="brand">
      <span class="brand__mark"></span>
      <span class="brand__name">Brightpath Horizon</span>
    </div>
    <div class="card__stripe"></div>
  </section>

  <section class="card card--back" aria-label="Card back">
    <div class="brand">
      <span class="brand__mark"></span>
      <span class="brand__name">Brightpath Horizon</span>
    </div>
    <div class="divider"></div>
    <div class="contact">
      <p class="contact__name">Daniel Carter</p>
      <p class="contact__role">FOUNDER</p>
      <p class="contact__address">47 Maplewood Cres<br>Toronto ON M4K 2B3</p>
      <ul class="contact__list">
        <li class="contact__item">
          <svg class="contact__icon" viewBox="0 0 14 14" aria-hidden="true"><path d="M4 0h6a1 1 0 0 1 1 1v12a1 1 0 0 1-1 1H4a1 1 0 0 1-1-1V1a1 1 0 0 1 1-1zm.5 1.5v9.5h5V1.5z"/></svg>
          (416) 555-0142
        </li>
        <li class="contact__item">
          <svg class="contact__icon" viewBox="0 0 14 14" aria-hidden="true"><path d="M3 0h8v4H3zM1 5h12a1 1 0 0 1 1 1v5h-3v3H3v-3H0V6a1 1 0 0 1 1-1zm3 5v3h6v-3z"/></svg>
          (416) 555-0187
        </li>
        <li class="contact__item">
          <svg class="contact__icon" viewBox="0 0 14 14" aria-hidden="true"><path d="M0 2h14v1L7 8 0 3zm0 2.5 7 5 7-5V12H0z"/></svg>
          dcarter@brightpathhome.net
        </li>
        <li class="contact__item">
          <svg class="contact__icon" viewBox="0 0 14 14" aria-hidden="true"><path d="M7 0a7 7 0 1 1 0 14A7 7 0 0 1 7 0zm0 1.4A5.6 5.6 0 1 0 7 12.6 5.6 5.6 0 0 0 7 1.4zM3 6h8v2H3z"/></svg>
          brightpathhome.com
        </li>
      </ul>
    </div>
    <div class="card__stripe"></div>
  </section>

</main>
</body>
</html>
```